Wordpress Design Project

Hi,

I would like a more modern colourful design doing for my website ZAP Lnx (www.za%plnx.com - remove percentage). But I do still want to keep the same sort of colors, just maybe lighter. More interesting.

I want the inside pages to NOT all look the same with just boring text.

I want the site to look more appealing and maybe a new logo.
Updates

I would like to mention I would prefer to keep the same logo after rethinking it (possibly a slight refresh of the logo if you feel its a good idea) and the same color scheme as at present.

Saves us rebranding a lot of our apps, tools online ads etc.

Also I thought it is worth mentioning we have 2 parts to the site. The front end and the logged in area. It would be good if when making the front end you keep in mind the back end at http://p.za%plnx.com (remove percentage). We can only edit this limitedly (can edit the entire footer, the logo and full CSS of it). Would be good if we could make sure the header and footer can be used on the back end as well maybe to make it match.

I also want layouts making not just for the homepage. Obviously every page will basically be the same but I don't want all the other pages to just be 'text' and no real layout.

You can see out main pages on the website at the moment, I want those other pages to be laid out nice and differently as well. For example the testimonials page could be more interesting with speech bubbles and pictures of each person (just use placeholders). The affiliates page could be a description and then a nice fancy list of features why to join etc. 

Nothing overly complicated but I think it makes the whole site seem a lot better.

Target Market(s)

Affiliate Marketing. International.

Requirements
Must have
• Needs to be more room for links across the navigation at the top, also sub menus (at present we have a lot of pages which are hidden deep within other pages).
Nice to have
• Lists of features for advertisers and affiliates on the homepage part.

Menu items and buttons have nice hover over effects.

I want to get across on our pages all the different unique features we have.

Maybe some kind of slider which has past offer logos in, just use example logos.

```html
<!DOCTYPE html>
<html lang="en">
<head>
<meta charset="utf-8">
<title>ZAP Lnx – Contact Us</title>
<link href="https://fonts.googleapis.com/css2?family=PT+Sans:wght@400;700&family=PT+Sans+Narrow:wght@400;700&family=Open+Sans:wght@300&display=swap" rel="stylesheet">
<style>
:root{
  --blue-deep:#0b5e9c;
  --blue-mid:#1e8fc8;
  --blue-light:#3ec3e6;
  --cyan:#20d0ea;
  --orange:#f7941d;
  --orange-dark:#e0700a;
  --orange-light:#fbb040;
  --heading-blue:#1a7fb5;
  --text-grey:#6b6b6b;
  --field-border:#c9c9c9;
  --white:#ffffff;
}
*{margin:0;padding:0;box-sizing:border-box}
html,body{width:1200px;height:1195px;overflow:hidden}
body{font-family:"PT Sans",sans-serif;background:var(--white);position:relative}
.site-header{position:absolute;left:0;top:0;width:1200px;height:127px;
  background:linear-gradient(180deg,#137fbf 0%,#1a9ad2 60%,#22a7dc 100%);border-top:4px solid #3a4a58}
.brand{position:absolute;left:90px;top:36px;color:var(--white)}
.brand-name{display:flex;align-items:center;gap:10px;font-family:"PT Sans",sans-serif;font-weight:700;font-size:50px;line-height:1;color:var(--orange)}
.brand-name .dot{width:16px;height:16px;border-radius:50%;background:var(--orange)}
.brand-tag{font-size:11px;font-weight:700;letter-spacing:2.6px;margin-top:4px;color:var(--white)}
.call{position:absolute;left:634px;top:12px;color:var(--white);font-size:18px}
.call strong{font-size:23px;font-weight:400;margin-left:4px}
.account{position:absolute;left:918px;top:0;width:190px;height:35px;background:#3a4650;
  clip-path:polygon(0 0,100% 0,96% 100%,4% 100%);color:var(--white);font-size:12px;font-weight:700;text-align:center;line-height:35px}
.search{position:absolute;left:887px;top:74px;width:181px;height:38px;background:var(--white);border-radius:4px;
  font-size:13px;color:#555;padding:12px 16px}
.search svg{position:absolute;right:10px;top:9px}
.go{position:absolute;left:1076px;top:75px;width:42px;height:37px;background:var(--orange);border-radius:4px;color:#5a3300;font-size:17px;text-align:center;line-height:37px}
.main-nav{position:absolute;left:0;top:127px;width:1200px;height:58px;
  background:linear-gradient(180deg,var(--orange-light),var(--orange) 60%,var(--orange-dark));display:flex;padding-left:145px}
.main-nav a{font-family:"PT Sans Narrow",sans-serif;font-size:21px;color:var(--white);text-decoration:none;padding:0 18px;line-height:54px}
.main-nav a.active{background:#d4670a}
.hero{position:absolute;left:0;top:185px;width:1200px;height:387px;
  background:radial-gradient(ellipse at 85% 100%,var(--cyan) 0%,var(--blue-mid) 30%,transparent 60%),linear-gradient(180deg,#1479ba,#0f67a8 60%,#0c5a9a)}
.hero-title{position:absolute;left:104px;top:52px;font-family:"Open Sans",sans-serif;font-weight:300;font-size:42px;color:var(--white)}
.hero-sub{position:absolute;left:106px;top:97px;font-size:28px;font-weight:700;color:var(--orange)}
.hero-text{position:absolute;left:104px;top:133px;width:420px;font-size:15px;line-height:24px;color:var(--white)}
.join{position:absolute;left:101px;top:237px;width:209px;height:60px;background:linear-gradient(180deg,#2f8fc7,#1f78b3);border-bottom:4px solid #0b4f82;border-radius:3px;
  color:var(--white);font-size:26px;font-weight:700;text-align:center;line-height:56px}
.arrows{position:absolute;left:103px;top:317px;display:flex;gap:8px}
.arrows span{width:30px;height:30px;border-radius:50%;background:#0a3a63;display:flex;align-items:center;justify-content:center}
.hero-art{position:absolute;left:565px;top:40px;width:500px;height:280px;border-radius:30px;
  background:radial-gradient(ellipse at center,rgba(214,226,232,.55),rgba(214,226,232,.15) 65%,transparent 75%)}
.contact{position:absolute;left:0;top:572px;width:1200px;height:463px}
.contact h1{position:absolute;left:93px;top:28px;font-size:26px;font-weight:400;color:var(--heading-blue)}
.form-intro{position:absolute;left:120px;top:100px;font-size:20px;color:#7a7a7a}
.field-label{position:absolute;left:120px;font-size:14px;color:var(--text-grey)}
.field{position:absolute;left:293px;width:249px;height:31px;border:1px solid var(--field-border);background:var(--white)}
.submit{position:absolute;left:432px;top:395px;width:111px;height:37px;background:linear-gradient(180deg,var(--orange-light),var(--orange-dark));border-radius:3px;
  color:var(--white);font-size:14px;font-weight:700;text-align:center;line-height:37px}
.divider{position:absolute;left:574px;top:106px;width:1px;height:313px;background:#ddd}
.map{position:absolute;left:606px;top:132px;width:256px;height:252px;border:1px solid #ccc;background:linear-gradient(135deg,#e8e4dc,#ddd8ce)}
.details{position:absolute;left:897px;top:242px}
.details h2{font-size:20px;font-weight:400;color:#5f6b72;display:flex;align-items:center;gap:12px}
.details h2 i{width:25px;height:25px;background:#dedede;border-radius:3px;display:inline-flex;align-items:center;justify-content:center}
.details p{font-size:13px;color:var(--text-grey);line-height:24px;margin-left:5px;margin-top:10px}
.details p+p{margin-top:0}
.site-footer{position:absolute;left:0;top:1035px;width:1200px;height:160px;
  background:linear-gradient(180deg,var(--cyan) 0%,#17a9d9 12%,#0f86c2 40%,#0c6aa8 100%)}
.footer-links{position:absolute;left:87px;top:27px;font-family:"PT Sans Narrow",sans-serif;font-size:14px;color:var(--white)}
.footer-links span{margin:0 7px}
.copy{position:absolute;left:87px;top:57px;font-size:13px;color:var(--white)}
.social{position:absolute;left:977px;top:29px;display:flex;gap:10px}
.social i{width:32px;height:32px;border-radius:3px;background:#2c6e9e;border:1px solid rgba(255,255,255,.4)}
</style>
</head>
<body>
<header class="site-header">
  <div class="brand">
    <div class="brand-name">ZAP Lnx<span class="dot"></span></div>
    <div class="brand-tag">EARN MONEY &amp; INCREASE SALES</div>
  </div>
  <div class="call">Call Us : <strong>+44 (0) 1632 960418</strong></div>
  <div class="account">USER LOG IN &nbsp;|&nbsp; REGISTER</div>
  <div class="search">Search
    <svg width="24" height="22" viewBox="0 0 24 22"><circle cx="9" cy="9" r="7" fill="none" stroke="#bbb" stroke-width="2.5"/><line x1="14" y1="14" x2="21" y2="20" stroke="#bbb" stroke-width="3"/></svg>
  </div>
  <div class="go">GO</div>
</header>
<nav class="main-nav">
  <a class="active">HOME</a><a>ABOUT US</a><a>OUR BLOG</a><a>TESTIMONIALS</a><a>AFFILIATES</a><a>ADVERTISERS</a><a>CONTACT US</a>
</nav>
<section class="hero">
  <h2 class="hero-title">International Affiliate Network</h2>
  <div class="hero-sub">Duis tincidunt lectus quis dui viverra</div>
  <p class="hero-text">Suspendisse vulputate aliquam dui. Nulla elementum dui ut augue. Aliquam vehicula mi at mauris. Maecenas placerat, nisl at consequat rhoncu</p>
  <div class="join">Join Us Today</div>
  <div class="arrows">
    <span><svg width="10" height="12"><polygon points="8,0 8,12 1,6" fill="#fff"/></svg></span>
    <span><svg width="10" height="12"><polygon points="2,0 2,12 9,6" fill="#fff"/></svg></span>
  </div>
  <div class="hero-art" role="img" aria-label="Illustration of business people standing on connected hexagon tiles forming a network"></div>
</section>
<main class="contact">
  <h1>Contact Us</h1>
  <div class="form-intro">Kindly post your valuable Suggestions &amp; Query</div>
  <div class="field-label" style="top:144px">Enter your Name</div>
  <div class="field" style="top:141px"></div>
  <div class="field-label" style="top:192px">Enter your Email</div>
  <div class="field" style="top:191px"></div>
  <div class="field-label" style="top:240px">Enter your Phone Number</div>
  <div class="field" style="top:241px"></div>
  <div class="field-label" style="top:288px">Add Your Comments Here:</div>
  <div class="field" style="top:283px;height:88px"></div>
  <div class="submit">SUBMIT QUERY</div>
  <div class="divider"></div>
  <div class="map" role="img" aria-label="Street map showing the office location"></div>
  <div class="details">
    <h2><i><svg width="12" height="16" viewBox="0 0 12 16"><path d="M3 1 L1 3 Q1 10 8 15 L11 13 L8 10 L6 11 Q4 8 4 6 L6 5 Z" fill="#fff"/></svg></i>Contact Details</h2>
    <p>#12 Harbour Road,Lorem ipsum,</p>
    <p>Phone: +44 (0)1632 960418</p>
    <p>Tollfree: +44 (0)1632 960418</p>
    <p>E-mail: info@zaplnx.com</p>
  </div>
</main>
<footer class="site-footer">
  <div class="footer-links">AFFILIATE TERMS &amp; CONDITIONS<span>|</span>ADVERTISER TERMS &amp; CONDITIONS<span>|</span>PRIVACY POLICY &amp; COOKIES<span>|</span>FAQ<span>|</span>CONTACT US</div>
  <div class="copy">© 2013 ZAP Media UK Ltd - All Rights Reserved.</div>
  <div class="social"><i aria-label="Social link"></i><i aria-label="Social link"></i><i aria-label="Social link"></i></div>
</footer>
</body>
</html>
```